Northvale Strategy Partners Website Design

I need a website design for my new business consulting and executive coaching firm, Northvale Strategy Partners. We provide consultative services to business C-suites as well as personal coaching to executives. I have attached the logo with color scheme I have chosen. I would like the website to reflect professionalism and continue the color scheme in the logo.

Target Market(s)

Small to medium business and their executives; middle to upper income men and women in mid- to late career looking for significance

Industry/Entity Type

Business Consultant

Number of Pages Required

4 page

Requirements
Must have
• A homepage with prominent logo and way to contact for more information; an area on the homepage with easy to read, clear text to describe what the company does; a prominent area on the homepage for a tagline; a blog page that can be updated regularly, an "about us" page with biographical information; an "about us" page; a page detailing services offered
• The web design must match the logo colors and font that I have uploaded.
Nice to have
• A lighthouse picture in the background or header
Should not have
• A lot of text area on the homepage

```html
<!DOCTYPE html>
<html lang="en">
<head>
<meta charset="utf-8">
<title>Northvale Strategy Partners</title>
<link rel="stylesheet" href="https://fonts.googleapis.com/css2?family=Marcellus&family=Montserrat:wght@500&family=Roboto:wght@400;500&display=swap">
<style>
  :root {
    --navy: #1f2f5c;
    --crimson: #7a1218;
    --ink: #1a1a1a;
    --body: #5a5a5a;
    --mist: #f1f1f1;
    --white: #ffffff;
    --footer: #1f1f1f;
    --footer-deep: #101010;
    --footer-line: #3a3a3a;
    --footer-text: #e8e8e8;
    --red-accent: #c0262d;
  }
  * { box-sizing: border-box; margin: 0; padding: 0; }
  html, body { width: 1200px; height: 2372px; overflow: hidden; background: var(--white); }
  body { position: relative; font-family: "Roboto", Arial, sans-serif; color: var(--body); }
  .abs { position: absolute; }
  .serif { font-family: "Marcellus", Georgia, serif; }

  /* Hero */
  .hero { position: absolute; left: 0; top: 0; width: 1200px; height: 677px; overflow: hidden; }
  .hero-photo { position: absolute; inset: 0;
    background: linear-gradient(100deg, #e6e9ee 0%, #f2f3f4 35%, #ecebe8 55%, #d8d2cc 75%, #cfcac6 100%); }
  .main-nav { position: absolute; left: 76px; top: 0; width: 1046px; height: 51px; border-bottom: 1.5px solid var(--crimson); }
  .main-nav a { position: absolute; top: 15px; font-family: "Marcellus", Georgia, serif; font-size: 16px; color: var(--ink); text-decoration: none; letter-spacing: .3px; }
  .main-nav a.is-active { color: var(--crimson); }
  .nav-marker { position: absolute; left: 297px; top: 44px; width: 0; height: 0;
    border-left: 6px solid transparent; border-right: 6px solid transparent; border-bottom: 6px solid var(--crimson); }
  .brand { position: absolute; left: 0; width: 1200px; top: 368px; text-align: center; }
  .brand-name { font-family: "Marcellus", Georgia, serif; font-size: 66px; color: var(--navy); line-height: 1; letter-spacing: 2px; }
  .brand-sub { display: inline-block; margin-top: 6px; padding: 2px 14px 0; border-top: 2px solid #6d6d6d;
    font-family: "Marcellus", Georgia, serif; font-size: 24px; color: #6d6d6d; letter-spacing: 2px; }
  .slide-btn { position: absolute; top: 487px; width: 57px; height: 57px; display: flex; align-items: center; justify-content: center;
    font-size: 28px; font-family: "Roboto", Arial, sans-serif; }
  .slide-prev { left: 541px; background: var(--navy); color: var(--white); }
  .slide-next { left: 602px; border: 1.5px solid var(--navy); color: var(--navy); }

  /* Welcome */
  .welcome { position: absolute; top: 677px; left: 0; width: 1200px; height: 408px; text-align: center; }
  .welcome-kicker { position: absolute; top: 55px; width: 100%; font-family: "Marcellus", Georgia, serif; font-size: 32px; color: var(--navy); }
  .welcome-title { position: absolute; top: 101px; width: 100%; font-family: "Marcellus", Georgia, serif; font-size: 32px; color: var(--crimson); }
  .welcome-text { position: absolute; top: 168px; left: 190px; width: 820px; font-size: 16px; line-height: 29.5px; color: var(--body); }
  .btn-outline { position: absolute; left: 506px; top: 292px; width: 186px; height: 57px; border: 1.5px solid var(--navy);
    display: flex; align-items: center; justify-content: center; font-family: "Marcellus", Georgia, serif; font-size: 16px; color: var(--navy); }

  /* Services */
  .services { position: absolute; top: 1085px; left: 0; width: 1200px; height: 415px; background: var(--mist); }
  .section-title { position: absolute; width: 100%; text-align: center; font-family: "Marcellus", Georgia, serif; font-size: 33px; color: var(--navy); }
  .section-title em { font-style: normal; color: var(--crimson); }
  .service { position: absolute; width: 380px; }
  .service-icon { position: absolute; left: -40px; top: -4px; width: 32px; height: 32px; }
  .service-title { font-family: "Montserrat", Arial, sans-serif; font-weight: 500; font-size: 21px; color: var(--ink); line-height: 26px; }
  .service-text { margin-top: 10px; font-size: 14.5px; line-height: 25px; color: var(--body); }

  /* Blog */
  .blog { position: absolute; top: 1500px; left: 0; width: 1200px; height: 506px; }
  .post-meta { position: absolute; width: 73px; text-align: right; }
  .post-day { font-family: "Roboto", Arial, sans-serif; font-weight: 500; font-size: 21px; color: var(--ink); line-height: 24px; }
  .post-month { font-size: 11.5px; color: var(--body); }
  .post-rule { margin: 12px 0 10px; border-top: 1.5px solid #8a8a8a; }
  .post-views { font-size: 11.5px; color: var(--body); }
  .post-photo { position: absolute; width: 313px; height: 157px; }
  .post-photo.meeting { background: linear-gradient(120deg, #d7dbe0 0%, #3a4354 40%, #e8e6e2 60%, #2b3140 100%); }
  .post-photo.desk { background: linear-gradient(120deg, #b49a80 0%, #e6ddd2 45%, #6c5440 70%, #d9cfc5 100%); }
  .post-title { position: absolute; font-family: "Montserrat", Arial, sans-serif; font-weight: 500; font-size: 19px; color: var(--ink); }
  .post-text { position: absolute; width: 340px; font-size: 14.5px; line-height: 25px; color: var(--body); }
  .btn-solid { position: absolute; width: 156px; height: 42px; background: var(--navy); color: var(--white);
    display: flex; align-items: center; justify-content: center; font-family: "Roboto", Arial, sans-serif; font-size: 17px; }

  /* Footer */
  .site-footer { position: absolute; top: 2006px; left: 0; width: 1200px; height: 313px; background: var(--footer); color: var(--footer-text); }
  .footer-brand { position: absolute; left: 110px; top: 90px; width: 230px; text-align: center; font-family: "Marcellus", Georgia, serif; color: var(--white); }
  .footer-brand-name { font-size: 25px; letter-spacing: 1px; line-height: 1; }
  .footer-brand-sub { display: inline-block; margin-top: 4px; border-top: 1.5px solid var(--white); padding-top: 2px; font-size: 11px; letter-spacing: 1px; }
  .social { position: absolute; top: 198px; width: 36px; height: 36px; background: #111; }
  .social.is-first { background: var(--crimson); }
  .social span { position: absolute; left: 13px; top: 13px; width: 10px; height: 10px; background: var(--white); }
  .footer-heading { position: absolute; top: 49px; font-family: "Marcellus", Georgia, serif; font-size: 18px; color: var(--white); }
  .footer-nav { position: absolute; left: 454px; top: 80px; width: 210px; list-style: none; }
  .footer-nav li { height: 39.5px; border-bottom: 1px solid var(--footer-line); padding-left: 32px; position: relative;
    font-family: "Marcellus", Georgia, serif; font-size: 16px; line-height: 37px; color: var(--footer-text); }
  .footer-nav li:last-child { border-bottom: 0; }
  .footer-nav li::before { content: ""; position: absolute; left: 8px; top: 14px;
    border-top: 5px solid transparent; border-bottom: 5px solid transparent; border-left: 5px solid var(--red-accent); }
  .quick-form { position: absolute; left: 759px; top: 90px; width: 363px; height: 122px; border: 1px solid var(--footer-line); }
  .quick-form .field { position: absolute; font-size: 11px; color: #8a8a8a; }
  .quick-form .row { position: absolute; left: 0; top: 0; width: 100%; height: 40px; border-bottom: 1px solid var(--footer-line); }
  .quick-form .split { position: absolute; left: 190px; top: 0; height: 40px; border-left: 1px solid var(--footer-line); }
  .btn-submit { position: absolute; left: 759px; top: 225px; width: 134px; height: 41px; border: 1.5px solid var(--crimson);
    display: flex; align-items: center; justify-content: center; font-family: "Marcellus", Georgia, serif; font-size: 15px; color: var(--white); }
  .copyright { position: absolute; top: 2319px; left: 0; width: 1200px; height: 53px; background: var(--footer-deep);
    text-align: center; line-height: 53px; font-size: 11.5px; color: var(--white); }
  .copyright em { font-style: normal; color: var(--red-accent); }
</style>
</head>
<body>

<header class="hero">
  <div class="hero-photo" role="img" aria-label="Smiling consultant in glasses in a bright office with blurred colleagues behind"></div>
  <nav class="main-nav">
    <a class="is-active" style="left:281px">HOME</a>
    <a style="left:391px">ABOUT US</a>
    <a style="left:536px">SERVICES</a>
    <a style="left:664px">CONTACT US</a>
    <span class="nav-marker"></span>
  </nav>
  <div class="brand">
    <div class="brand-name">NORTHVALE</div>
    <div class="brand-sub">STRATEGY PARTNERS</div>
  </div>
  <div class="slide-btn slide-prev">&laquo;</div>
  <div class="slide-btn slide-next">&raquo;</div>
</header>

<section class="welcome">
  <h2 class="welcome-kicker" style="font-weight:400">WELCOME TO</h2>
  <h1 class="welcome-title" style="font-weight:400">NORTHVALE STRATEGY PARTNERS</h1>
  <p class="welcome-text">Lorem ipsum dolor sit amet, consectetur adipiscing elit, sed do eiusmod tempor incididunt ut labore et dolore magna aliqua. Ut enim ad minim veniam, quis nostrud exercitation ullamco laboris nisi ut aliquip ex ea commodo consequat. Duis aute irure dolor in reprehenderit.</p>
  <div class="btn-outline">READ MORE</div>
</section>

<section class="services">
  <h2 class="section-title" style="top:54px;font-weight:400">KNOW WHAT <em>WE DO</em></h2>

  <div class="service" style="left:256px;top:137px">
    <svg class="service-icon" viewBox="0 0 32 32"><circle cx="13" cy="9" r="6" fill="#111"/><path d="M2 30c0-8 5-12 11-12s11 4 11 12z" fill="#111"/><rect x="21" y="14" width="9" height="7" rx="1" fill="#111"/></svg>
    <div class="service-title">Consultative Services</div>
    <p class="service-text">Lorem ipsum dolor sit amet, consectetur adipiscing elit, sed do eiusmod tempor incididunt.</p>
  </div>
  <div class="service" style="left:672px;top:137px">
    <svg class="service-icon" viewBox="0 0 32 32"><circle cx="10" cy="9" r="5" fill="#111"/><circle cx="22" cy="9" r="5" fill="#111"/><path d="M1 30c0-8 4-13 9-13s9 5 9 13zM13 30c0-8 4-13 9-13s9 5 9 13z" fill="#111"/></svg>
    <div class="service-title">Executive Coaching</div>
    <p class="service-text">Lorem ipsum dolor sit amet, consectetur adipiscing elit, sed do eiusmod tempor incididunt.</p>
  </div>
  <div class="service" style="left:256px;top:268px">
    <svg class="service-icon" viewBox="0 0 32 32"><circle cx="16" cy="16" r="11" fill="none" stroke="#111" stroke-width="4"/><path d="M11 16l4 4 7-8" fill="none" stroke="#111" stroke-width="3"/></svg>
    <div class="service-title">Lorem Ipsume dolor</div>
    <p class="service-text">Lorem ipsum dolor sit amet, consectetur adipiscing elit, sed do eiusmod tempor incididunt.</p>
  </div>
  <div class="service" style="left:672px;top:268px">
    <svg class="service-icon" viewBox="0 0 32 32"><circle cx="18" cy="13" r="11" fill="none" stroke="#111" stroke-width="2.5"/><text x="18" y="18" font-size="13" font-family="Arial" text-anchor="middle" fill="#111">$</text><path d="M1 28c5 0 9-2 12-5" fill="none" stroke="#111" stroke-width="3"/></svg>
    <div class="service-title">Lorem Ipsume dolor</div>
    <p class="service-text">Lorem ipsum dolor sit amet, consectetur adipiscing elit, sed do eiusmod tempor incididunt.</p>
  </div>
</section>

<section class="blog">
  <h2 class="section-title" style="top:55px;font-weight:400">OUR LATEST <em>BLOG</em></h2>

  <div class="post-meta" style="left:180px;top:150px">
    <div class="post-day">29</div>
    <div class="post-month">Dec - 2015</div>
    <div class="post-rule"></div>
    <svg width="16" height="10" viewBox="0 0 16 10"><path d="M1 5c4-6 10-6 14 0-4 6-10 6-14 0z" fill="#222"/><circle cx="8" cy="5" r="2" fill="#fff"/></svg>
    <div class="post-views">20 - View</div>
  </div>
  <div class="post-photo meeting" style="left:266px;top:128px" role="img" aria-label="Three colleagues in business suits discussing around a table"></div>
  <div class="post-title" style="left:268px;top:300px">Lorem Ipsume dolor</div>
  <p class="post-text" style="left:268px;top:335px">Lorem ipsum dolor sit amet, consectetur adipiscing elit, sed do eiusmod tempor incididunt.</p>
  <div class="btn-solid" style="left:266px;top:400px">View More</div>

  <div class="post-meta" style="left:607px;top:150px">
    <div class="post-day">29</div>
    <div class="post-month">Dec - 2015</div>
    <div class="post-rule"></div>
    <svg width="16" height="10" viewBox="0 0 16 10"><path d="M1 5c4-6 10-6 14 0-4 6-10 6-14 0z" fill="#222"/><circle cx="8" cy="5" r="2" fill="#fff"/></svg>
    <div class="post-views">20 - View</div>
  </div>
  <div class="post-photo desk" style="left:692px;top:128px" role="img" aria-label="Person relaxing at a desk beside a laptop in warm window light"></div>
  <div class="post-title" style="left:694px;top:300px">Lorem Ipsume dolor</div>
  <p class="post-text" style="left:694px;top:335px">Lorem ipsum dolor sit amet, consectetur adipiscing elit, sed do eiusmod tempor incididunt.</p>
  <div class="btn-solid" style="left:692px;top:400px">View More</div>
</section>

<footer class="site-footer">
  <div class="footer-brand">
    <div class="footer-brand-name">NORTHVALE</div>
    <div class="footer-brand-sub">STRATEGY PARTNERS</div>
  </div>
  <a class="social is-first" style="left:145px"><span></span></a>
  <a class="social" style="left:186px"><span></span></a>
  <a class="social" style="left:228px"><span></span></a>
  <a class="social" style="left:270px"><span></span></a>

  <h3 class="footer-heading" style="left:454px;font-weight:400">NAVIGATION</h3>
  <ul class="footer-nav">
    <li>Home</li>
    <li>About Us</li>
    <li>Services</li>
    <li>Blog</li>
    <li>Contact Us</li>
  </ul>

  <h3 class="footer-heading" style="left:760px;font-weight:400">QUICK CONTACT US</h3>
  <div class="quick-form">
    <div class="row"></div>
    <div class="split"></div>
    <span class="field" style="left:14px;top:13px">Name</span>
    <span class="field" style="left:204px;top:13px">Name</span>
    <span class="field" style="left:14px;top:53px">Message</span>
  </div>
  <div class="btn-submit">SUBMIT</div>
</footer>

<div class="copyright">&copy; <em>NORTHVALE STRATEGY PARTNERS</em> - 2015. All Rights Reserved</div>

</body>
</html>
```